Tree Pruning Website

We need a website for a tree Arborist, pruning company called Maple Crest Canopy Works. We look after all types of trees, knock down trees and prune trees. Our target market is from domestic clients to government clients and everything in between.

We would like to see the use of our main colours which are orange and green

We are not looking forward in seeing a template that we have seen before but a unique template. We have designed 5 templates ourselves and we wish for the design community to take our designs to the next level.

We have also designed a template for things that **we are not** looking for (Version 4)

To make it fair for everyone, we are also not giving out any participation payments as we have had. One winner will take all of the payment!!!

I Have attached a image of the designs and a image of a tree.

We are just looking at the PSD file been developed. We have our own team who can slice the image up into a HTML format.

Target Market(s)

Everyone who needs to cut down a tree

Industry/Entity Type

Government

Requirements
Must have
• Logo on front page
A List of our services
jQuery slider on page
Phone Number on every page

```html
<!DOCTYPE html>
<html lang="en">
<head>
<meta charset="utf-8">
<title>Maple Crest Canopy Works</title>
<link href="https://fonts.googleapis.com/css2?family=Dosis:wght@400;500;600&family=Cabin:wght@400;500;600&display=swap" rel="stylesheet">
<style>
:root{
  --orange:#f07a1a;
  --orange-dark:#c94e06;
  --green:#3f9a1c;
  --ink:#3a3a3a;
  --nav-text:#5a5a5a;
  --footer:#2a2526;
  --footer-bar:#3b3637;
  --footer-text:#e8e6e6;
  --muted:#9a9596;
}
*{box-sizing:border-box;margin:0;padding:0}
html,body{width:1200px;height:1200px;overflow:hidden}
body{position:relative;background:#fff;font-family:"Cabin",sans-serif;color:var(--ink)}
.header-backdrop{position:absolute;left:0;top:0;width:1200px;height:441px;
  background:radial-gradient(ellipse at 8% 40%,#b9b9b9 0,#d6d6d6 25%,rgba(230,230,230,0) 55%),
             radial-gradient(ellipse at 96% 70%,#c4c4c4 0,rgba(230,230,230,0) 40%),
             linear-gradient(#e6e6e6,#f0f0f0);
  border-bottom:1px solid #d9d9d9}
.brand{position:absolute;left:106px;top:-2px;width:335px;height:118px;background:linear-gradient(#f4f4f4,#e9e9e9);
  border:1px solid #c9c9c9;border-top:none;border-radius:0 0 10px 10px;display:flex;align-items:center;gap:12px;padding-left:18px}
.brand-dot{width:46px;height:46px;border-radius:50%;background:var(--green);flex:none}
.brand-name{font-family:"Dosis",sans-serif;font-weight:600;font-size:30px;line-height:32px;color:var(--green)}
.call{position:absolute;right:113px;top:26px;font-family:"Cabin",sans-serif;font-size:21px;color:#4a4a4a;display:flex;align-items:center;gap:8px}
.main-nav{position:absolute;left:467px;top:75px;width:617px;height:40px;border-radius:8px;
  background:linear-gradient(#fbfbfb,#e6e6e6 60%,#b7b7b7);box-shadow:0 1px 2px rgba(0,0,0,.2)}
.main-nav a{position:absolute;top:10px;font-family:"Dosis",sans-serif;font-size:18px;color:var(--nav-text);text-decoration:none}
.slider{position:absolute;left:111px;top:133px;width:977px;height:390px;border-radius:8px;overflow:hidden;box-shadow:0 0 3px rgba(0,0,0,.3)}
.slide-photo{position:absolute;inset:0;background:linear-gradient(160deg,#5d7fae 0,#6f8e52 30%,#4a6a22 55%,#c9c4b0 78%,#7c7a5a 100%)}
.slide-caption{position:absolute;left:0;bottom:0;width:100%;height:83px;background:rgba(20,20,20,.88);color:#fff;
  font-size:16px;line-height:30px;padding:12px 14px}
.slide-arrow{position:absolute;top:172px;width:50px;height:50px}
.col-title{position:absolute;top:542px;font-family:"Dosis",sans-serif;font-size:26px;color:var(--orange);font-weight:400}
.thumb{position:absolute;top:586px;width:290px;height:159px;border:1px solid #d8d8d8;background:#fff;padding:5px;box-shadow:0 1px 2px rgba(0,0,0,.1)}
.thumb div{width:100%;height:100%}
.col-text{position:absolute;top:751px;width:276px;font-size:12.6px;line-height:20px;text-align:justify;color:#333}
.service-list{position:absolute;top:797px;left:467px;width:260px;list-style:none;display:grid;grid-template-columns:98px 150px;row-gap:14px;font-size:14px;color:#333}
.service-list li{display:flex;align-items:center;gap:10px;line-height:20px}
.service-list li::before{content:"";border-left:7px solid #333;border-top:5px solid transparent;border-bottom:5px solid transparent}
.btn{position:absolute;top:883px;width:94px;height:35px;border-radius:6px;background:linear-gradient(#f59a3b,#e0650c 55%,#c8500a);
  border:1px solid #a8440a;color:#3a1a05;font-size:15px;text-align:center;line-height:33px;text-decoration:none}
.footer{position:absolute;left:0;top:935px;width:1200px;height:212px;background:radial-gradient(ellipse at 50% 30%,#3e3839 0,var(--footer) 60%);color:var(--footer-text)}
.footer h3{position:absolute;font-family:"Dosis",sans-serif;font-weight:400;font-size:26px}
.newsletter-input{position:absolute;left:125px;top:66px;width:277px;height:34px;border-radius:17px;background:#fff;display:flex;align-items:center;gap:8px;padding-left:12px;font-size:12.5px;color:#666}
.newsletter-note{position:absolute;left:247px;top:113px;font-size:12.5px}
.subscribe{position:absolute;left:301px;top:143px;width:87px;height:35px;border-radius:17px;border:1px solid #6a6465;background:#3a3435;
  color:#fff;font-size:16px;font-weight:600;text-align:center;line-height:33px}
.contact-line{position:absolute;font-size:13.5px;display:flex;align-items:center;gap:10px}
.map{position:absolute;left:824px;top:29px;width:282px;height:119px;border:1px solid #999;background:linear-gradient(135deg,#e6e2d8,#d7d2c4 60%,#e9e4b0)}
.social{position:absolute;top:167px;width:32px;height:32px;border-radius:50%;background:#b5b1b1}
.footer-bar{position:absolute;left:0;top:1147px;width:1200px;height:53px;background:var(--footer-bar)}
.footer-bar a{position:absolute;top:11px;font-family:"Dosis",sans-serif;font-size:18px;color:#d9d6d6;text-decoration:none}
.copyright{position:absolute;left:908px;top:21px;font-size:11.5px;color:var(--muted)}
</style>
</head>
<body>
<div class="header-backdrop"></div>

<header>
  <div class="brand">
    <span class="brand-dot"></span>
    <span class="brand-name">Maple Crest<br>Canopy Works</span>
  </div>
  <div class="call">
    <svg width="22" height="18" viewBox="0 0 22 18"><path d="M3 3c2-2 4-2 5 0l1 3-2 2c1 2 3 4 5 5l2-2 3 1c2 1 2 3 0 5-6 1-14-7-14-14z" fill="#555"/></svg>
    Call us : 555 014 2290
  </div>
  <nav class="main-nav">
    <a style="left:31px">Home</a><a style="left:98px">About Us</a><a style="left:189px">Our Services</a>
    <a style="left:306px">Our Work</a><a style="left:402px">Get a Quote</a><a style="left:509px">Contact Us</a>
  </nav>
</header>

<section class="slider">
  <div class="slide-photo" role="img" aria-label="Looking up into the canopy of a tall white-barked gum tree against blue sky"></div>
  <svg class="slide-arrow" style="left:10px" viewBox="0 0 50 50"><circle cx="25" cy="25" r="23" fill="rgba(0,0,0,.55)" stroke="#fff" stroke-width="3"/><path d="M29 17 19 25l10 8z" fill="#fff"/></svg>
  <svg class="slide-arrow" style="right:10px" viewBox="0 0 50 50"><circle cx="25" cy="25" r="23" fill="rgba(0,0,0,.55)" stroke="#fff" stroke-width="3"/><path d="M21 17l10 8-10 8z" fill="#fff"/></svg>
  <p class="slide-caption">At vero eos et accusamus et iusto odio dignissimos ducimus qui blanditiis praesentium voluptatum deleniti atque corrupti quos dolores et quas molestias excepturi sint</p>
</section>

<main>
  <h2 class="col-title" style="left:129px">Who we are?</h2>
  <div class="thumb" style="left:129px"><div role="img" aria-label="Lone tree in a green field under a blue sky" style="background:linear-gradient(#2a55a8,#7aa6d8 45%,#3d7a1f 62%,#6a9a22)"></div></div>
  <p class="col-text" style="left:137px">Lorem Ipsum is simply dummy text of the printing and typesetting industry. occaecati cupiditate non provident, similique sunt in culpa qui officia deserunt mollitia animi, id est laborum et dolorum fuga. Et harum quidem rerum facilis est et expedita distinctio.</p>
  <a class="btn" style="left:132px">View more</a>

  <h2 class="col-title" style="left:460px">Our Services</h2>
  <div class="thumb" style="left:458px"><div role="img" aria-label="Lush green tree canopy in a forest" style="background:linear-gradient(160deg,#b8d89a,#4f9a2a 40%,#2f6e16)"></div></div>
  <p class="col-text" style="left:466px">Lorem Ipsum is simply dummy text of the printing and typesetting industry.</p>
  <ul class="service-list">
    <li>Diagnosis</li><li>Tree Purning</li><li>Treatment</li><li>Tree Removal</li>
  </ul>
  <a class="btn" style="left:462px">View more</a>

  <h2 class="col-title" style="left:791px">Tree Pruning</h2>
  <div class="thumb" style="left:787px"><div role="img" aria-label="Arborist in safety gear roped up while cutting a tree" style="background:linear-gradient(160deg,#7a5248,#5a6a3a 45%,#3f6a22 75%,#6a5a3a)"></div></div>
  <p class="col-text" style="left:789px;width:273px">Lorem Ipsum is simply dummy text of the printing and typesetting industry. occaecati cupiditate non provident, similique sunt in culpa qui officia deserunt mollitia animi, id est laborum et dolorum fuga. Et harum quidem rerum facilis est et expedita distinctio.</p>
  <a class="btn" style="left:786px">View more</a>
</main>

<footer class="footer">
  <h3 style="left:130px;top:24px">News Letter</h3>
  <div class="newsletter-input">
    <svg width="24" height="18" viewBox="0 0 24 18"><rect x="1" y="1" width="22" height="16" fill="#888"/><path d="M1 1l11 9 11-9M1 17l8-7M23 17l-8-7" stroke="#fff" stroke-width="1.5" fill="none"/></svg>
    Subscribe your news letter
  </div>
  <p class="newsletter-note">Subscribe your news letter</p>
  <div class="subscribe">Subscribe</div>

  <h3 style="left:481px;top:24px">Contact info.</h3>
  <div class="contact-line" style="left:473px;top:72px"><svg width="14" height="13" viewBox="0 0 14 13"><path d="M7 0 0 6h2v7h4V9h2v4h4V6h2z" fill="#ddd"/></svg>42 Birchwood Ln</div>
  <div class="contact-line" style="left:500px;top:103px">Fernvale</div>
  <div class="contact-line" style="left:500px;top:134px">Oakshire 100482</div>
  <div class="contact-line" style="left:616px;top:72px"><svg width="15" height="13" viewBox="0 0 22 18"><path d="M3 3c2-2 4-2 5 0l1 3-2 2c1 2 3 4 5 5l2-2 3 1c2 1 2 3 0 5-6 1-14-7-14-14z" fill="#ddd"/></svg>+1 555 010 4471</div>
  <div class="contact-line" style="left:616px;top:103px"><svg width="12" height="14" viewBox="0 0 12 14"><path d="M0 0h8l4 4v10H0z" fill="#ddd"/></svg>+1 555 013 8826</div>
  <div class="contact-line" style="left:616px;top:134px"><svg width="14" height="11" viewBox="0 0 14 11"><rect x=".5" y=".5" width="13" height="10" fill="none" stroke="#ddd"/><path d="M.5.5 7 6 13.5.5" stroke="#ddd" fill="none"/></svg>hello@maplecrest.example</div>

  <div class="map" role="img" aria-label="Street map showing the office location"></div>
  <span class="social" style="left:904px" aria-label="Social link"></span>
  <span class="social" style="left:946px" aria-label="Social link"></span>
  <span class="social" style="left:988px" aria-label="Social link"></span>
  <span class="social" style="left:1030px" aria-label="Social link"></span>
  <svg class="social" style="left:1071px;background:none" viewBox="0 0 32 32"><circle cx="16" cy="16" r="16" fill="#b5b1b1"/><path d="M13 7h6v6h6v6h-6v6h-6v-6H7v-6h6z" fill="#2a2526"/></svg>
</footer>

<nav class="footer-bar">
  <a style="left:128px">Home</a><a style="left:195px">About Us</a><a style="left:286px">Our Services</a>
  <a style="left:403px">Our Work</a><a style="left:499px">Get a Quote</a><a style="left:607px">Contact Us</a>
  <span class="copyright">©maplecrest.example 2013, All Rights Reserved</span>
</nav>
</body>
</html>
```